Southern Plantskills Academy needs a modern website that oozes professionalism

Our current website is boring and looks like everyone elses. We need a modern website that says we are the best at plant operator training. We use Brontovex and Hiraketo equipment for our training. We train all over Australia in Civil Construction, Mining and Quarrying. We want to be the "Go to" website for all plant operator training in Australia.

Industry/Entity Type

Heavy Machinery Training

Colors
0054AA
0677BA
7BADD7
CADEEF
E8F1F8
FFF300
FFF600
FEFA6F
FFFEC7
FFFEE8

```html
<!DOCTYPE html>
<html lang="en">
<head>
<meta charset="utf-8">
<title>Southern Plantskills Academy</title>
<link href="https://fonts.googleapis.com/css2?family=Poppins:wght@400;500;600;700&family=Open+Sans:wght@400;600&display=swap" rel="stylesheet">
<style>
:root{
  --navy:#0b2a5b;
  --blue:#0054AA;
  --blue-mid:#0677BA;
  --blue-soft:#7BADD7;
  --blue-pale:#E8F1F8;
  --yellow:#F9C712;
  --yellow-soft:#FEFA6F;
  --dark:#101b2b;
  --ink:#1d2633;
  --muted:#6b7380;
  --grey:#f1f2f4;
  --white:#ffffff;
}
*{margin:0;padding:0;box-sizing:border-box}
html,body{width:1200px;height:4964px;overflow:hidden}
body{position:relative;background:var(--white);font-family:'Open Sans',Arial,sans-serif;color:var(--ink)}
h1,h2,h3,h4,.brand,.btn,.tag,.nav a{font-family:'Poppins',Arial,sans-serif}
.abs{position:absolute}
.btn{display:inline-flex;align-items:center;justify-content:center;font-weight:600;font-size:14px;text-transform:uppercase;letter-spacing:.5px;border:none}
.btn-yellow{background:var(--yellow);color:var(--navy);border-radius:4px}
.tag{font-size:12px;font-weight:600;color:var(--yellow);text-transform:uppercase;letter-spacing:1.5px;display:flex;align-items:center;gap:10px}
.tag::before,.tag::after{content:"";width:40px;height:2px;background:var(--yellow)}
.tag.left::after{display:none}
.section-title{font-size:48px;font-weight:700;color:var(--navy);line-height:1.2}
.center{left:0;width:1200px;text-align:center;justify-content:center}
.ph{display:block}

/* header */
.topbar{top:0;left:0;width:1200px;height:72px;background:var(--white)}
.brand{display:flex;align-items:center;gap:12px;font-weight:700;color:var(--navy);font-size:15px;line-height:1.1;text-transform:uppercase}
.brand .mark{width:34px;height:34px;border-radius:50%;background:var(--yellow)}
.info{display:flex;align-items:center;gap:12px;font-size:12px;color:var(--muted);line-height:1.4}
.info strong{display:block;color:var(--navy);font-family:'Poppins',sans-serif;font-size:12px;text-transform:uppercase}
.info svg{width:28px;height:28px}
.quote-btn{top:16px;left:930px;width:172px;height:44px;background:var(--navy);color:var(--white);font-size:12px}
.nav{top:80px;left:88px;width:1024px;height:48px;background:var(--white);display:flex;align-items:center;padding:0 24px;gap:44px;box-shadow:0 4px 14px rgba(0,0,0,.12);z-index:3}
.nav a{font-size:14px;font-weight:500;color:var(--navy);text-decoration:none}
.social{margin-left:auto;display:flex;gap:8px}
.social span{width:28px;height:28px;border-radius:3px;background:var(--blue)}
.social span:nth-child(2){background:#c8283a}
.social span:nth-child(3){background:var(--blue-mid)}

/* hero */
.hero{top:72px;left:0;width:1200px;height:720px;background:linear-gradient(180deg,#4a4540 0%,#6b5f52 45%,#3c352f 100%)}
.hero-shade{top:72px;left:0;width:1200px;height:720px;background:rgba(10,15,25,.35)}
.hero .welcome{top:260px;left:552px;width:96px;height:26px;background:var(--blue);color:var(--white);font-size:11px;border-radius:2px}
.hero h1{top:300px;left:0;width:1200px;text-align:center;font-size:58px;line-height:1.15;font-weight:600;color:var(--white)}
.hero .about-btn{top:472px;left:532px;width:136px;height:40px;border:1.5px solid var(--white);color:var(--white);font-size:11px;background:transparent}
.arrow-box{width:44px;height:56px;background:var(--white);display:flex;align-items:center;justify-content:center}
.arrow-box svg{width:16px;height:16px}

/* about */
.about-img{top:932px;left:110px;width:420px;height:420px;border-radius:50%;background:linear-gradient(160deg,#9fb7cf 0%,#c7a14a 55%,#7a6a4c 100%);border:8px solid var(--navy)}
.about-badge{top:1222px;left:430px;width:110px;height:110px;border-radius:50%;background:var(--white);box-shadow:0 6px 18px rgba(0,0,0,.15);display:flex;align-items:center;justify-content:center}
.about-badge span{width:46px;height:46px;border-radius:50%;background:var(--blue)}
.about-text{left:608px;width:480px}
.about-text h2{font-size:44px;line-height:1.2;font-weight:700;color:var(--navy)}
.about-text p{font-size:14px;line-height:1.75;color:var(--muted);margin-bottom:20px}

/* services */
.services-bg{top:1448px;left:0;width:1200px;height:848px;background:var(--grey)}
.svc-card{top:1680px;width:328px;height:312px;border-radius:8px;overflow:hidden}
.svc-card .photo{position:absolute;inset:0}
.svc-card .shade{position:absolute;inset:0;background:linear-gradient(180deg,rgba(10,20,40,.15),rgba(10,20,40,.75))}
.svc-card .icon{position:absolute;top:40px;left:32px;width:64px;height:64px;border-radius:8px;background:var(--white);display:flex;align-items:center;justify-content:center}
.svc-card .icon svg{width:34px;height:34px}
.svc-card h3{position:absolute;top:150px;left:32px;font-size:24px;font-weight:600;color:var(--white)}
.svc-card p{position:absolute;top:192px;left:32px;width:264px;font-size:12px;line-height:1.5;color:#e5e7ea}
.svc-card .more{position:absolute;top:240px;left:32px;font-family:'Poppins',sans-serif;font-size:14px;font-weight:600;color:var(--white);padding-bottom:12px;width:264px;border-bottom:3px solid var(--yellow)}
.svc-arrows{top:1556px;left:1004px;display:flex;gap:8px}
.svc-arrows .arrow-box{width:48px;height:48px;border-radius:4px}

/* cta */
.cta{top:2176px;left:96px;width:1016px;height:208px;border-radius:10px;background:linear-gradient(90deg,#0e1726 0%,#24303f 55%,#3a3c3e 100%);display:flex;align-items:center;padding:0 64px}
.cta h3{font-size:26px;line-height:1.3;font-weight:600;color:var(--white)}
.cta .get{position:absolute;left:588px;top:84px;width:164px;height:48px;border:1.5px solid var(--white);color:var(--white);background:transparent;font-size:13px;text-transform:none}
.cta .call{position:absolute;left:768px;top:84px;width:196px;height:48px;background:var(--white);color:var(--navy);font-size:14px;gap:8px;text-transform:none;border-radius:2px}

/* projects */
.proj{top:2592px;height:400px;border-radius:8px}
.proj-caption{top:2872px;left:246px;width:680px;height:80px;background:var(--white);display:flex;align-items:center;padding-left:36px;font-family:'Poppins',sans-serif;font-size:24px;font-weight:600;color:var(--navy)}
.proj-caption .go{position:absolute;right:0;top:0;width:80px;height:80px;background:var(--yellow);display:flex;align-items:center;justify-content:center}

/* reviews */
.rev-bg{top:3056px;left:340px;width:860px;height:528px;background:var(--grey)}
.rev-img{top:3056px;left:0;width:340px;height:528px;background:linear-gradient(160deg,#2c2a27,#5a4c3a 60%,#26221e)}
.rev-card{top:3256px;width:328px;height:196px;background:var(--white);border-radius:4px;box-shadow:0 6px 18px rgba(0,0,0,.08);padding:26px 24px}
.rev-card p{font-size:12px;line-height:1.7;color:var(--muted)}
.rev-card .who{position:absolute;left:24px;bottom:22px;display:flex;align-items:center;gap:12px;font-family:'Poppins',sans-serif;font-size:13px;font-weight:600;color:var(--navy)}
.rev-card .avatar{width:40px;height:40px;border-radius:50%;background:#b9a58f}
.rev-card .qm{position:absolute;right:22px;bottom:14px;font-family:Georgia,serif;font-size:52px;line-height:1;color:var(--navy)}
.dots{top:3500px;left:628px;display:flex;gap:10px;align-items:center}
.dots span{width:8px;height:8px;border-radius:50%;background:#c3c8cf}
.dots span.on{width:14px;height:14px;border:2px solid var(--blue);background:var(--white)}

/* contact */
.contact-card{top:3832px;left:88px;width:1024px;height:448px;background:var(--white);box-shadow:0 8px 30px rgba(0,0,0,.1)}
.contact-photo{position:absolute;left:0;top:0;width:424px;height:448px;background:linear-gradient(160deg,#d9c26a,#8d8472 55%,#3b4a5c)}
.phone-pill{position:absolute;left:200px;top:336px;width:200px;height:60px;background:var(--white);display:flex;align-items:center;justify-content:center;gap:10px;font-family:'Poppins',sans-serif;font-weight:600;font-size:18px;color:var(--navy)}
.form{position:absolute;left:464px;top:48px;width:512px}
.form h3{font-size:26px;font-weight:600;color:var(--navy);margin-bottom:10px}
.form p{font-size:13px;line-height:1.6;color:var(--muted);margin-bottom:24px}
.field{height:52px;border:1px solid #dfe2e6;font-size:13px;color:var(--muted);display:flex;align-items:center;padding-left:16px;margin-bottom:18px}
.row{display:flex;gap:16px}
.row .field{flex:1}
.send{width:100%;height:56px}

/* footer */
.footer{top:4400px;left:0;width:1200px;height:504px;background:var(--dark)}
.strip{top:4380px;left:88px;width:1024px;height:168px;background:var(--white);box-shadow:0 8px 24px rgba(0,0,0,.1);display:flex}
.strip div{flex:1;display:flex;flex-direction:column;align-items:center;justify-content:center;gap:14px;font-family:'Poppins',sans-serif;font-weight:600;font-size:16px;color:var(--navy);border-right:1px solid #e3e6ea}
.strip div:last-child{border-right:none}
.strip svg{width:40px;height:40px}
.foot-brand{top:4628px;left:96px;color:var(--white);font-size:18px}
.foot-brand .mark{width:44px;height:44px}
.foot-about{top:4716px;left:96px;width:360px;font-size:12px;line-height:1.7;color:#a9b0ba}
.newsletter{top:4784px;left:440px;display:flex}
.foot-col h4{font-size:17px;font-weight:600;color:var(--white);margin-bottom:8px}
.foot-col .bar{width:40px;height:2px;background:var(--yellow);margin-bottom:20px}
.foot-col li{list-style:none;font-size:13px;color:#a9b0ba;line-height:2.4}
.bottom{top:4904px;left:0;width:1200px;height:60px;background:var(--blue-pale);display:flex;align-items:center;padding:0 24px;font-size:13px;color:var(--navy)}
.bottom .social{gap:10px}
.bottom .social span{width:14px;height:14px;border-radius:2px;background:var(--navy)}
</style>
</head>
<body>

<!-- Header -->
<div class="abs topbar">
  <div class="abs brand" style="top:16px;left:100px"><span class="mark"></span><span>Southern<br>Plantskills Academy</span></div>
  <div class="abs info" style="top:16px;left:470px">
    <svg viewBox="0 0 24 24" fill="none" stroke="#0054AA" stroke-width="2"><path d="M12 22s7-7 7-12a7 7 0 0 0-14 0c0 5 7 12 7 12z"/><circle cx="12" cy="10" r="2.5"/></svg>
    <div><strong>Location</strong>12 Quarry Rd, Dubbo</div>
  </div>
  <div class="abs info" style="top:16px;left:690px">
    <svg viewBox="0 0 24 24" fill="none" stroke="#0054AA" stroke-width="2"><circle cx="12" cy="12" r="9"/><path d="M12 7v5l3 2"/></svg>
    <div><strong>Office Hours</strong>6:00 to 17:00 (Mon-Fri)</div>
  </div>
  <div class="abs btn quote-btn">Request a Quote</div>
</div>

<!-- Hero -->
<section>
  <div class="abs hero" role="img" aria-label="Yellow dump truck and excavator working in a quarry"></div>
  <div class="abs hero-shade"></div>
  <nav class="abs nav">
    <a>Home</a><a>About Us</a><a>Services</a><a>Gallery</a><a>Our Team</a><a>Contact Us</a>
    <div class="social"><span></span><span></span><span></span></div>
  </nav>
  <div class="hero">
    <div class="abs btn welcome">Welcome</div>
    <h1 class="abs">Empowering Operators,<br>Fueling Progress</h1>
    <div class="abs btn about-btn">About Company</div>
  </div>
  <div class="abs arrow-box" style="top:484px;left:40px"><svg viewBox="0 0 16 16"><path d="M10 3 5 8l5 5" fill="none" stroke="#0b2a5b" stroke-width="2"/></svg></div>
  <div class="abs arrow-box" style="top:484px;left:1116px"><svg viewBox="0 0 16 16"><path d="m6 3 5 5-5 5" fill="none" stroke="#0b2a5b" stroke-width="2"/></svg></div>
</section>

<!-- About -->
<section>
  <div class="abs about-img" role="img" aria-label="Operator in hi-vis vest beside a yellow wheel loader"></div>
  <div class="abs about-badge"><span></span></div>
  <div class="abs tag left" style="top:940px;left:608px">About Us</div>
  <div class="abs about-text" style="top:972px">
    <h2>Training Operators<br>for Industry Leaders</h2>
  </div>
  <div class="abs about-text" style="top:1108px">
    <p>Our trainers bring decades of site experience to every course. We teach safe, confident operation on Brontovex and Hiraketo plant, with practical hours on real civil, mining and quarry sites across every Australian state.</p>
    <p>From first-time operators to seasoned crews seeking new tickets, each program is built around nationally recognised units and tailored to the machines your projects depend on.</p>
  </div>
  <div class="abs btn btn-yellow" style="top:1292px;left:608px;width:168px;height:48px;text-transform:none">Apply Now</div>
</section>

<!-- Services -->
<section>
  <div class="abs services-bg"></div>
  <div class="abs tag left" style="top:1532px;left:88px">Services</div>
  <h2 class="abs section-title" style="top:1568px;left:88px">Services We Offer</h2>
  <div class="abs svc-arrows">
    <div class="arrow-box"><svg viewBox="0 0 16 16"><path d="M10 3 5 8l5 5" fill="none" stroke="#0b2a5b" stroke-width="2"/></svg></div>
    <div class="arrow-box"><svg viewBox="0 0 16 16"><path d="m6 3 5 5-5 5" fill="none" stroke="#0b2a5b" stroke-width="2"/></svg></div>
  </div>

  <article class="abs svc-card" style="left:88px">
    <div class="photo" role="img" aria-label="Excavator on a civil construction site" style="background:linear-gradient(160deg,#c9a13c,#6d5a3a)"></div>
    <div class="shade"></div>
    <div class="icon"><svg viewBox="0 0 24 24" fill="none" stroke="#0054AA" stroke-width="1.8"><path d="M3 20h18M5 20V10l7-5 7 5v10M10 20v-5h4v5"/></svg></div>
    <h3>Civil Construction</h3>
    <p>Earthmoving tickets for roads, subdivisions and major infrastructure.</p>
    <div class="more">Read More</div>
  </article>
  <article class="abs svc-card" style="left:440px">
    <div class="photo" role="img" aria-label="Haul truck at an open-cut mine" style="background:linear-gradient(160deg,#a88f6b,#5b4633)"></div>
    <div class="shade"></div>
    <div class="icon"><svg viewBox="0 0 24 24" fill="none" stroke="#0054AA" stroke-width="1.8"><path d="M4 20 14 10M12 4l8 8-3 3-8-8z"/></svg></div>
    <h3>Mining</h3>
    <p>Surface mining plant courses with hands-on haul and dozer time.</p>
    <div class="more">Read More</div>
  </article>
  <article class="abs svc-card" style="left:788px">
    <div class="photo" role="img" aria-label="Loader working a quarry stockpile" style="background:linear-gradient(160deg,#d3a64e,#7a5431)"></div>
    <div class="shade"></div>
    <div class="icon"><svg viewBox="0 0 24 24" fill="none" stroke="#0054AA" stroke-width="1.8"><path d="M3 19h18L15 8l-4 6-3-3z"/></svg></div>
    <h3>Quarrying</h3>
    <p>Loader, excavator and crusher feed training for quarry crews.</p>
    <div class="more">Read More</div>
  </article>

  <div class="abs btn btn-yellow" style="top:2064px;left:516px;width:168px;height:48px;text-transform:none">Contact Us</div>
</section>

<!-- CTA -->
<section class="abs cta" role="img" aria-label="Dark band over construction machinery">
  <h3>Where Operators Thrive<br>and Industries Flourish</h3>
  <div class="btn get">Get A Quote</div>
  <div class="btn call">
    <svg width="16" height="16" viewBox="0 0 24 24" fill="#0b2a5b"><path d="M6.6 10.8a15 15 0 0 0 6.6 6.6l2.2-2.2a1 1 0 0 1 1-.25 11 11 0 0 0 3.6.6 1 1 0 0 1 1 1V20a1 1 0 0 1-1 1A17 17 0 0 1 3 4a1 1 0 0 1 1-1h3.5a1 1 0 0 1 1 1 11 11 0 0 0 .6 3.6 1 1 0 0 1-.25 1z"/></svg>
    +61 400 218 775
  </div>
</section>

<!-- Projects -->
<section>
  <div class="abs tag center" style="top:2456px">Our Work</div>
  <h2 class="abs section-title center" style="top:2484px;display:flex">Latest Projects</h2>
  <div class="abs proj" role="img" aria-label="Excavator on a muddy work site" style="left:0;width:172px;border-radius:0 8px 8px 0;background:linear-gradient(160deg,#8a7b68,#4f4336)"></div>
  <div class="abs proj" role="img" aria-label="Yellow wheel loader at sunset" style="left:212px;width:756px;background:linear-gradient(180deg,#9ec3e0 0%,#d9c7a0 55%,#6b5c45 100%)"></div>
  <div class="abs proj" role="img" aria-label="Wheel loader on a haul road" style="left:1000px;width:200px;border-radius:8px 0 0 8px;background:linear-gradient(160deg,#a9bcc8,#7c6a4e)"></div>
  <div class="abs proj-caption">Project 567 in ABC State
    <div class="go"><svg width="22" height="22" viewBox="0 0 16 16"><path d="M3 8h9M8 4l4 4-4 4" fill="none" stroke="#fff" stroke-width="2"/></svg></div>
  </div>
  <div class="abs arrow-box" style="top:2764px;left:84px;border-radius:2px"><svg viewBox="0 0 16 16"><path d="M10 3 5 8l5 5" fill="none" stroke="#0b2a5b" stroke-width="2"/></svg></div>
  <div class="abs arrow-box" style="top:2764px;left:1020px;border-radius:2px"><svg viewBox="0 0 16 16"><path d="m6 3 5 5-5 5" fill="none" stroke="#0b2a5b" stroke-width="2"/></svg></div>
</section>

<!-- Reviews -->
<section>
  <div class="abs rev-bg"></div>
  <div class="abs rev-img" role="img" aria-label="Machinery on a dark construction site"></div>
  <div class="abs tag" style="top:3108px;left:560px">Testimonials</div>
  <h2 class="abs section-title" style="top:3136px;left:480px">Reviews from Clients</h2>

  <div class="abs rev-card" style="left:144px">
    <p>The trainers knew the machines inside out. I left with my excavator ticket and the confidence to run it on a live site the next week. Highly recommend the whole crew.</p>
    <div class="who"><span class="avatar" role="img" aria-label="Reviewer portrait"></span>Mara Kelling</div>
    <div class="qm">&rdquo;</div>
  </div>
  <div class="abs rev-card" style="left:504px">
    <p>The trainers knew the machines inside out. I left with my excavator ticket and the confidence to run it on a live site the next week. Highly recommend the whole crew.</p>
    <div class="who"><span class="avatar" role="img" aria-label="Reviewer portrait"></span>Mara Kelling</div>
    <div class="qm">&rdquo;</div>
  </div>
  <div class="abs rev-card" style="left:872px">
    <p>The trainers knew the machines inside out. I left with my excavator ticket and the confidence to run it on a live site the next week. Highly recommend the whole crew.</p>
    <div class="who"><span class="avatar" role="img" aria-label="Reviewer portrait"></span>Mara Kelling</div>
    <div class="qm">&rdquo;</div>
  </div>
  <div class="abs dots"><span class="on"></span><span></span><span></span><span></span></div>
</section>

<!-- Contact -->
<section>
  <div class="abs tag center" style="top:3704px">Contact Us</div>
  <h2 class="abs section-title center" style="top:3732px;display:flex">Get in touch with us</h2>
  <div class="abs contact-card">
    <div class="contact-photo" role="img" aria-label="Two operators in hard hats reviewing plans beside machinery"></div>
    <div class="phone-pill">
      <svg width="18" height="18" viewBox="0 0 24 24" fill="#0b2a5b"><path d="M6.6 10.8a15 15 0 0 0 6.6 6.6l2.2-2.2a1 1 0 0 1 1-.25 11 11 0 0 0 3.6.6 1 1 0 0 1 1 1V20a1 1 0 0 1-1 1A17 17 0 0 1 3 4a1 1 0 0 1 1-1h3.5a1 1 0 0 1 1 1 11 11 0 0 0 .6 3.6 1 1 0 0 1-.25 1z"/></svg>
      1800-274-391
    </div>
    <div class="form">
      <h3>Get Free Consultation</h3>
      <p>Get a free consultation from our experts. Our customer support team help you 24/7. Don't hesitate.</p>
      <div class="field">Your Name</div>
      <div class="row"><div class="field">Your Email</div><div class="field">Message</div></div>
      <div class="btn btn-yellow send">Get In Touch</div>
    </div>
  </div>
</section>

<!-- Footer -->
<footer>
  <div class="abs footer"></div>
  <div class="abs strip">
    <div><svg viewBox="0 0 24 24" fill="none" stroke="#F9C712" stroke-width="1.8"><path d="M12 22s7-7 7-12a7 7 0 0 0-14 0c0 5 7 12 7 12z"/><circle cx="12" cy="10" r="2.5"/></svg>Come to Our Location</div>
    <div><svg viewBox="0 0 24 24" fill="none" stroke="#F9C712" stroke-width="1.8"><rect x="3" y="5" width="18" height="14" rx="2"/><path d="m3 7 9 6 9-6"/></svg>Send Us an Email</div>
    <div><svg viewBox="0 0 24 24" fill="none" stroke="#F9C712" stroke-width="1.8"><path d="M6.6 10.8a15 15 0 0 0 6.6 6.6l2.2-2.2a1 1 0 0 1 1-.25 11 11 0 0 0 3.6.6 1 1 0 0 1 1 1V20a1 1 0 0 1-1 1A17 17 0 0 1 3 4a1 1 0 0 1 1-1h3.5a1 1 0 0 1 1 1 11 11 0 0 0 .6 3.6 1 1 0 0 1-.25 1z"/></svg>Give Us a Call</div>
  </div>
  <div class="abs brand foot-brand"><span class="mark"></span><span>Southern<br>Plantskills Academy</span></div>
  <p class="abs foot-about">Nationally recognised plant operator training for civil, mining and quarry crews, delivered on site or at our yards across Australia.</p>
  <div class="abs newsletter">
    <div style="width:170px;height:40px;background:var(--white);font-size:12px;color:var(--muted);display:flex;align-items:center;padding-left:12px">Enter your email...</div>
    <div class="btn btn-yellow" style="height:40px;width:96px;border-radius:0;font-size:12px">Subscribe</div>
  </div>
  <div class="abs foot-col" style="top:4612px;left:548px">
    <h4>Visit Our Place</h4><div class="bar"></div>
    <ul><li>12 Quarry Rd</li><li>Dubbo NSW 2830</li><li>hello@plantskills.example</li></ul>
  </div>
  <div class="abs foot-col" style="top:4612px;left:788px">
    <h4>Useful Links</h4><div class="bar"></div>
    <ul><li>About Us</li><li>Practice area</li><li>Why Choose Us</li><li>How it works</li><li>News &amp; Updates</li></ul>
  </div>
  <div class="abs foot-col" style="top:4664px;left:960px">
    <ul><li>Testimonials</li><li>FAQs</li><li>Contact</li><li>Contact Us</li><li>Privacy Policy</li></ul>
  </div>
  <div class="abs bottom">Southern Plantskills Academy
    <div class="social"><span></span><span></span><span></span><span></span></div>
  </div>
</footer>

</body>
</html>
```